holloway paving service

Needs to have phone number 0418259730 and email markholloway@brightmail.com.au.
ABN 62318470915
name mark holloway

For all your concreting solutions
Excavation
Exposed & colour concrete
House & shed slabs
Driveways
Landing & steps

Contact Information for Business Card

ph 0418259730
email markholloway@brightmail.com.au.
ABN 62318470915
name mark holloway

```html
<!DOCTYPE html>
<html lang="en">
<head>
<meta charset="utf-8">
<title>Holloway Paving Service – Business Card</title>
<link href="https://fonts.googleapis.com/css2?family=Montserrat:wght@500;600&family=Lato:wght@400;700&display=swap" rel="stylesheet">
<style>
  :root {
    --backdrop: #1c1c1d;
    --card: #222223;
    --card-edge: #2a2a2b;
    --orange: #f26a1b;
    --white: #f4f4f4;
    --emboss: #3a3a3c;
    --emboss-light: #5a5a5d;
    --emboss-text: #8d8d90;
  }
  * { margin: 0; padding: 0; box-sizing: border-box; }
  html, body { width: 1200px; height: 900px; overflow: hidden; }
  body {
    background: var(--backdrop);
    font-family: 'Lato', sans-serif;
    color: var(--white);
    position: relative;
  }
  .card {
    position: absolute;
    left: 250px;
    width: 700px;
    height: 390px;
    background: linear-gradient(135deg, var(--card) 0%, var(--card-edge) 60%, var(--card) 100%);
    box-shadow: 0 10px 30px rgba(0,0,0,.6);
  }
  .card--back { top: 40px; }
  .card--front { top: 470px; }
  .accent { color: var(--orange); }

  /* Back side */
  .brand-emboss {
    position: absolute;
    left: 160px; top: 125px;
    display: flex; align-items: center; gap: 16px;
  }
  .brand-emboss__mark {
    width: 80px; height: 80px;
    background: var(--emboss);
    transform: rotate(45deg);
    box-shadow: -1px -1px 0 var(--emboss-light);
    margin: 0 16px;
  }
  .brand-emboss__rule { width: 1px; height: 100px; background: var(--emboss-light); }
  .brand-emboss__text { display: flex; flex-direction: column; align-items: center; white-space: nowrap; }
  .brand-emboss__name {
    font-family: 'Montserrat', sans-serif; font-weight: 600;
    font-size: 26px; letter-spacing: 1px; color: var(--emboss-text);
    text-shadow: 0 1px 0 #111; line-height: 1.1;
  }
  .brand-emboss__sub {
    display: flex; align-items: center; gap: 12px; width: 100%;
    font-family: 'Montserrat', sans-serif; font-weight: 500;
    font-size: 18px; letter-spacing: 5px; color: var(--emboss-text); line-height: 1.1;
  }
  .brand-emboss__sub::before, .brand-emboss__sub::after {
    content: ""; flex: 1; height: 1px; background: var(--emboss-text);
  }
  .brand-emboss__phone {
    font-family: 'Montserrat', sans-serif; font-weight: 500;
    font-size: 18px; letter-spacing: 5px; color: var(--emboss-text); line-height: 1.1;
  }
  .card__web-back {
    position: absolute; left: 0; right: 0; bottom: 34px;
    text-align: center; font-size: 17px;
  }

  /* Front side */
  .brand {
    position: absolute; left: 50px; top: 150px;
    display: flex; align-items: center; gap: 14px;
  }
  .brand__mark { width: 46px; height: 46px; background: var(--orange); }
  .brand__rule { width: 2px; height: 66px; background: var(--orange); }
  .brand__text { display: flex; flex-direction: column; align-items: center; white-space: nowrap; }
  .brand__name {
    font-family: 'Montserrat', sans-serif; font-weight: 600;
    font-size: 15px; letter-spacing: .5px; color: var(--orange); line-height: 1.2;
  }
  .brand__sub {
    display: flex; align-items: center; gap: 8px; width: 100%;
    font-family: 'Montserrat', sans-serif; font-weight: 500;
    font-size: 12px; letter-spacing: 3px; color: var(--white); line-height: 1.2;
  }
  .brand__sub::before, .brand__sub::after {
    content: ""; flex: 1; height: 1px; background: var(--white);
  }
  .brand__phone {
    font-family: 'Montserrat', sans-serif; font-weight: 500;
    font-size: 12px; letter-spacing: 3px; color: var(--orange); line-height: 1.2;
  }
  .divider {
    position: absolute; left: 360px; top: 80px;
    width: 2px; height: 200px; background: var(--orange);
  }
  .details { position: absolute; left: 385px; top: 78px; }
  .details__name {
    font-family: 'Montserrat', sans-serif; font-weight: 500;
    font-size: 28px; letter-spacing: 1.5px; color: var(--orange); line-height: 1;
    white-space: nowrap;
  }
  .details__role { font-size: 16px; margin-top: 4px; }
  .details__locality { font-size: 16px; color: var(--orange); margin-top: 12px; }
  .details__address { font-size: 17px; }
  .contact { list-style: none; margin-top: 12px; }
  .contact li { display: flex; align-items: center; gap: 10px; font-size: 17px; line-height: 1.4; white-space: nowrap; }
  .contact svg { width: 12px; height: 12px; flex: none; }
  .contact__label { color: var(--orange); }
</style>
</head>
<body>
  <section class="card card--back">
    <div class="brand-emboss">
      <div class="brand-emboss__mark"></div>
      <div class="brand-emboss__rule"></div>
      <div class="brand-emboss__text">
        <span class="brand-emboss__name">HOLLOWAY PAVING</span>
        <span class="brand-emboss__sub">SERVICE</span>
        <span class="brand-emboss__phone">0418259730</span>
      </div>
    </div>
    <p class="card__web-back">www.<span class="accent">hollowaypaving</span>.com.au</p>
  </section>

  <section class="card card--front">
    <div class="brand">
      <div class="brand__mark"></div>
      <div class="brand__rule"></div>
      <div class="brand__text">
        <span class="brand__name">HOLLOWAY PAVING</span>
        <span class="brand__sub">SERVICE</span>
        <span class="brand__phone">0418259730</span>
      </div>
    </div>
    <div class="divider"></div>
    <div class="details">
      <h1 class="details__name">MARK HOLLOWAY</h1>
      <p class="details__role">Director</p>
      <p class="details__locality">Riverside</p>
      <p class="details__address">Launceston, Tasmania 7250</p>
      <ul class="contact">
        <li>
          <svg viewBox="0 0 12 12" aria-hidden="true"><path d="M2 1h3l1 3-1.5 1a6 6 0 0 0 2.5 2.5L8 6l3 1v3a1 1 0 0 1-1 1A9 9 0 0 1 1 2a1 1 0 0 1 1-1z" fill="#f26a1b"/></svg>
          +61 418 259 730
        </li>
        <li>
          <svg viewBox="0 0 12 12" aria-hidden="true"><rect x="1" y="2.5" width="10" height="7" fill="none" stroke="#f26a1b" stroke-width="1.2"/><path d="M1 2.5l5 4 5-4" fill="none" stroke="#f26a1b" stroke-width="1.2"/></svg>
          markholloway@brightmail.com.au
        </li>
        <li>
          <svg viewBox="0 0 12 12" aria-hidden="true"><circle cx="6" cy="6" r="5" fill="none" stroke="#f26a1b" stroke-width="1.1"/><ellipse cx="6" cy="6" rx="2.2" ry="5" fill="none" stroke="#f26a1b" stroke-width="1"/><path d="M1 6h10" stroke="#f26a1b" stroke-width="1"/></svg>
          <span>www.<span class="accent">hollowaypaving</span>.com.au</span>
        </li>
        <li>
          <svg viewBox="0 0 12 12" aria-hidden="true"></svg>
          <span><span class="contact__label">ABN</span> 62318470915</span>
        </li>
      </ul>
    </div>
  </section>
</body>
</html>
```